Meadowlark Property Review is a leading provider of residential appraisal and home inspection products in S

I need a business card/logo designed that obviously describes my business. We are a residential appraisal and home inspection company in Springfield, MO. We offer residential appraisals, home inspection, pest inspection and radon gas measurement. We have been in business for 18 years and hold state certified residential appraisal licenses and OBREX certified home inspection licenses. I have a logo that I really like and will attach, but would be open to new suggestions. I like more modern designs than traditional and would like a two sided card with our services, licenses and qualifications on the back.

```html
<!DOCTYPE html>
<html lang="en">
<head>
<meta charset="utf-8">
<title>Meadowlark Property Review – Business Card</title>
<link rel="stylesheet" href="https://fonts.googleapis.com/css2?family=Source+Sans+3:ital,wght@0,400;0,600;1,400&display=swap">
<style>
  :root {
    --backdrop: #3a3a3a;
    --card-white: #fafafa;
    --brown: #8b6a42;
    --brown-dark: #7a5c38;
    --orange: #ef8a1f;
    --text-grey: #4a4a4a;
    --rule: #9a9a9a;
    --back-text: #fbf6ee;
  }
  * { margin: 0; padding: 0; box-sizing: border-box; }
  html, body {
    width: 1200px; height: 750px; overflow: hidden;
    background: var(--backdrop);
    font-family: "Source Sans 3", "Myriad Pro", Arial, sans-serif;
  }
  .canvas { position: relative; width: 1200px; height: 750px; }

  .card {
    position: absolute; top: 228px;
    width: 461px; height: 262px;
  }
  .card--front { left: 124px; background: var(--card-white); }
  .card--back { left: 618px; background: var(--brown); }

  /* front */
  .brand {
    position: absolute; left: 200px; top: 52px; width: 240px;
    display: flex; align-items: center; justify-content: center; gap: 8px;
  }
  .brand__square { width: 10px; height: 10px; background: var(--orange); flex: none; }
  .brand__name {
    font-size: 19px; font-weight: 600; color: var(--brown); white-space: nowrap;
  }
  .accent-bar {
    position: absolute; left: 0; top: 129px; width: 6px; height: 30px;
    background: var(--brown);
  }
  .person { position: absolute; left: 28px; top: 126px; }
  .person__name { font-size: 17px; font-weight: 600; color: var(--brown); line-height: 1.2; }
  .person__title { font-size: 13px; color: var(--orange); line-height: 1.3; }
  .title-rule {
    position: absolute; left: 108px; top: 155px; width: 320px; height: 1px;
    background: var(--rule);
  }
  .contacts { position: absolute; left: 28px; top: 172px; list-style: none; }
  .contacts li {
    display: flex; align-items: center; gap: 6px;
    font-size: 11.5px; color: var(--text-grey); height: 17.6px;
  }
  .contacts svg { width: 12px; height: 12px; fill: var(--brown-dark); flex: none; }
  .address {
    position: absolute; right: 34px; top: 207px; text-align: right;
    font-size: 11.5px; color: var(--text-grey); line-height: 17.6px; font-style: normal;
  }

  /* back */
  .back-name {
    position: absolute; left: 0; right: 0; top: 112px; text-align: center;
    font-size: 24px; font-weight: 600; color: var(--back-text);
  }
  .services {
    position: absolute; left: 0; right: 0; top: 198px; text-align: center;
    font-size: 12px; font-style: italic; color: var(--back-text); line-height: 18px;
  }
  .services__dot {
    display: inline-block; width: 5px; height: 5px; border-radius: 50%;
    background: var(--orange); vertical-align: middle; margin: 0 3px;
  }
</style>
</head>
<body>
<main class="canvas">
  <section class="card card--front" aria-label="Card front">
    <div class="brand">
      <span class="brand__square"></span>
      <span class="brand__name">Meadowlark Property Review</span>
    </div>
    <span class="accent-bar"></span>
    <div class="person">
      <p class="person__name">Daniel Reyes</p>
      <p class="person__title">CEO/Founder</p>
    </div>
    <span class="title-rule"></span>
    <ul class="contacts">
      <li>
        <svg viewBox="0 0 24 24" aria-hidden="true"><path d="M6.6 10.8a15 15 0 0 0 6.6 6.6l2.2-2.2c.3-.3.7-.4 1-.2 1.1.4 2.3.6 3.6.6.6 0 1 .4 1 1V20c0 .6-.4 1-1 1A17 17 0 0 1 3 4c0-.6.4-1 1-1h3.5c.6 0 1 .4 1 1 0 1.3.2 2.5.6 3.6.1.3 0 .7-.2 1z"/></svg>
        417 555 0182
      </li>
      <li>
        <svg viewBox="0 0 24 24" aria-hidden="true"><path d="M6 3h12v5H6zM3 9h18v8h-3v-3H6v3H3zM7 15h10v6H7z"/></svg>
        417 555 0194
      </li>
      <li>
        <svg viewBox="0 0 24 24" aria-hidden="true"><path d="M2 5h20v14H2zm2 2v.5l8 5.5 8-5.5V7z"/></svg>
        daniel@meadowlarkreview.com
      </li>
      <li>
        <svg viewBox="0 0 24 24" aria-hidden="true"><path d="M12 2a10 10 0 1 0 0 20 10 10 0 0 0 0-20zm-1 17.9A8 8 0 0 1 4.2 10L9 15v1c0 1.1.9 2 2 2zm6.9-2.5c-.3-.8-1-1.4-1.9-1.4h-1v-3c0-.6-.4-1-1-1H8v-2h2c.6 0 1-.4 1-1V7h2c1.1 0 2-.9 2-2v-.4a8 8 0 0 1 2.9 12.8z"/></svg>
        www.meadowlarkreview.com
      </li>
    </ul>
    <address class="address">
      2140 Larkspur Avenue<br>
      Springfield, Missouri 65804
    </address>
  </section>

  <section class="card card--back" aria-label="Card back">
    <p class="back-name">Meadowlark Property Review</p>
    <p class="services">
      Residential appraisals <span class="services__dot"></span> Home inspection<br>
      Pest inspection and radon gas measurement.
    </p>
  </section>
</main>
</body>
</html>
```